Brenwick Structures Construction Company Seeking Modern Website

We are a small construction company wanting to create a web presence. We don't have much in the way of current content but will get photos as they come in. Attached is a picture of our business card.
The pages we would like on the menu are:
Home
Portfolio
Product Specs
Testimonials
Our Process
Contact
Some designs we like are:
http://www.tovasheds-example.com/
http://www.qrnstructures-example.com/
http://dunholtbarns-example.com/
http://pellingframes-example.com/
Not much requirements other than that so feel free to be creative!
Updates
Target Market(s)
Construction
Commercial and Residential Buildings
Industry/Entity Type
Construction Company
Number of Pages Required
5+ page
Look and feel

```html
<!DOCTYPE html>
<html lang="en">
<head>
<meta charset="utf-8">
<title>Brenwick Structures</title>
<link href="https://fonts.googleapis.com/css2?family=Raleway:wght@400;500;600&family=Open+Sans:wght@400;600;700&family=Khand:wght@500&display=swap" rel="stylesheet">
<style>
:root{
  --red:#f42e1c;
  --orange:#f26522;
  --cyan:#11b2e0;
  --ink:#222;
  --muted:#555;
  --grey-bg:#f2f2f2;
  --tab-grey:#e3e3e3;
  --footer:#3d3d3d;
  --white:#fff;
}
*{margin:0;padding:0;box-sizing:border-box}
html,body{width:809px;height:1200px;overflow:hidden}
body{position:relative;background:var(--grey-bg);font-family:"Open Sans",Arial,sans-serif;color:var(--ink)}
.abs{position:absolute}
.hero{left:0;top:0;width:809px;height:412px;background:linear-gradient(180deg,#a9c6e4 0%,#c9d9e8 22%,#8b5a44 38%,#7a4d3a 52%,#4f7a2f 66%,#5c8c36 100%)}
.site-header{left:54px;top:0;width:704px;height:84px;background:var(--white);border-radius:0 0 4px 4px;box-shadow:0 1px 4px rgba(0,0,0,.25)}
.brand{position:absolute;left:18px;top:30px;font-family:"Raleway",sans-serif;font-weight:600;font-size:15px;color:var(--red);display:flex;align-items:center;gap:6px;white-space:nowrap}
.brand-mark{width:12px;height:12px;background:var(--red)}
.contact-mini{position:absolute;top:21px;font-size:8px;line-height:11px;color:#444;display:flex;gap:8px;align-items:center;white-space:nowrap}
.contact-mini svg{width:16px;height:16px;flex:none}
.contact-mini b{font-weight:600;color:#333}
.nav a{position:absolute;top:56px;height:20px;line-height:20px;padding:0 8px;font-family:"Raleway",sans-serif;font-size:10.5px;color:#333;text-decoration:none;white-space:nowrap}
.nav a.active{background:var(--red);color:var(--white)}
.hero-caption{left:56px;top:168px;width:362px;height:100px;background:rgba(40,40,40,.55);padding:12px 12px}
.hero-caption h1{font-family:"Raleway",sans-serif;font-weight:500;font-size:26px;color:var(--red);line-height:30px;white-space:nowrap}
.hero-caption p{font-family:Arial,sans-serif;font-size:9.4px;line-height:14.5px;color:var(--white);margin-top:8px;white-space:nowrap}
.categories{left:50px;top:382px;width:714px;height:210px;background:var(--white)}
.categories-frame{position:absolute;left:12px;top:18px;width:692px;height:173px;border:1px solid #ccc}
.tab{position:absolute;left:12px;width:185px;height:40px;background:var(--tab-grey);display:flex;align-items:center;gap:8px;padding-left:10px;font-family:"Raleway",sans-serif;font-weight:500;font-size:14px;color:#222}
.tab svg{width:26px;height:26px}
.tab.active{background:var(--red);color:var(--white)}
.cat-copy{position:absolute;left:212px;top:10px;width:380px}
.cat-copy h2{font-family:"Raleway",sans-serif;font-weight:500;font-size:12.5px;line-height:18px;color:#222}
.cat-copy p{font-family:"Raleway",sans-serif;font-size:8.6px;line-height:13.2px;color:#555;margin-top:6px}
.cat-copy p+p{margin-top:13px}
.services-title{left:0;top:630px;width:809px;text-align:center;font-family:"Raleway",sans-serif;font-weight:400;font-size:19px;letter-spacing:1px;color:#222}
.services-rule{left:170px;top:666px;width:497px;height:1px;background:#d5d5d5}
.services-accent{left:369px;top:665px;width:73px;height:3px;background:var(--red)}
.service{width:292px;height:103px;background:var(--white)}
.service-strip{position:absolute;left:0;top:0;width:39px;height:100%;background:var(--red)}
.service-icon{position:absolute;left:9px;top:21px;width:60px;height:60px;border-radius:50%;background:var(--cyan);display:flex;align-items:center;justify-content:center}
.service-icon svg{width:24px;height:24px}
.service h3{position:absolute;left:82px;top:14px;font-family:"Raleway",sans-serif;font-weight:500;font-size:14px;letter-spacing:.3px;color:#222;white-space:nowrap}
.service p{position:absolute;left:82px;top:37px;width:205px;font-size:9.4px;line-height:13.2px;color:#333}
.service a{position:absolute;left:82px;top:77px;font-size:7.6px;font-weight:700;text-decoration:none}
.read-cyan{color:var(--cyan)}
.read-orange{color:var(--orange)}
.site-footer{left:0;top:973px;width:809px;height:201px;background:var(--footer);color:var(--white)}
.footer-title{position:absolute;top:34px;font-family:"Khand",sans-serif;font-weight:500;font-size:19px;color:#eee;white-space:nowrap}
.project{position:absolute;left:98px;width:162px;height:44px;background:#cfcfcf;display:flex}
.project-thumb{width:60px;height:44px;background:linear-gradient(135deg,#8a8f93,#cfd2d4 55%,#a88f70)}
.project-info{padding:5px 6px;font-size:7px;line-height:10px;color:#222;white-space:nowrap}
.project-info .street{font-size:8px;color:#777;font-weight:600}
.project-info b{font-weight:700}
.contact-row{position:absolute;left:318px;display:flex;font-size:7.6px;line-height:11px;white-space:nowrap}
.contact-row svg{width:10px;height:10px;margin-right:12px;margin-top:1px}
.contact-row .label{color:var(--red);font-weight:600;width:42px}
.form-label{position:absolute;left:511px;font-size:8.5px;font-weight:700}
.form-input{position:absolute;left:545px;width:136px;height:17px;background:var(--white)}
.subscribe{position:absolute;left:611px;top:131px;width:70px;height:20px;background:#c4d3dc;color:#222;font-size:9px;display:flex;align-items:center;justify-content:center}
.copyright{left:0;top:1174px;width:809px;height:26px;background:var(--red);color:var(--white);font-family:Arial,sans-serif;font-size:7.5px;display:flex;align-items:center;justify-content:center}
</style>
</head>
<body>

<div class="abs hero" role="img" aria-label="Photograph of a large brick family house with a green lawn and a brick mailbox in front"></div>

<header class="abs site-header">
  <div class="brand"><span class="brand-mark"></span>Brenwick Structures</div>
  <div class="contact-mini" style="left:417px">
    <svg viewBox="0 0 16 16" fill="none" stroke="#f26522" stroke-width="1.3"><path d="M2 8 8 2.5 14 8M4 7v7h8V7M7 14v-4h2v4"/></svg>
    <div><b>48 Larchmont Way</b><br>Dunmore, IL 60917</div>
  </div>
  <div class="contact-mini" style="left:575px">
    <svg viewBox="0 0 16 16" fill="none" stroke="#f26522" stroke-width="1.3"><path d="M4 2h3l1 3-2 1.5a7 7 0 0 0 3 3L10.5 8l3 1v3c0 1-1 2-2 2A10 10 0 0 1 2 4c0-1 1-2 2-2z"/></svg>
    <div><b>555-018-2247</b><br>hello@brenwick-example.com</div>
  </div>
  <nav class="nav">
    <a class="active" style="left:235px">Home</a>
    <a style="left:295px">Portfolio</a>
    <a style="left:367px">Product Specs</a>
    <a style="left:465px">Testimonials</a>
    <a style="left:556px">Our Process</a>
    <a style="left:643px">Contact</a>
  </nav>
</header>

<div class="abs hero-caption">
  <h1>Brenwick Structures</h1>
  <p>With strong roots in the Amish and farming communities of northern India-<br>na, we have personal experience with equipment storage, livestock barns</p>
</div>

<section class="abs categories">
  <div class="categories-frame">
    <div class="tab active" style="top:15px">
      <svg viewBox="0 0 26 26" fill="none" stroke="#111" stroke-width="2.4"><path d="M2 13 13 3l11 10M6 11v11h14V11"/><path d="M9 17h8"/></svg>RESIDENTIAL
    </div>
    <div class="tab" style="top:64px">
      <svg viewBox="0 0 26 26" fill="#111"><rect x="3" y="8" width="8" height="16"/><rect x="12" y="3" width="11" height="21"/><rect x="14" y="6" width="2" height="2" fill="#e3e3e3"/><rect x="19" y="6" width="2" height="2" fill="#e3e3e3"/><rect x="14" y="11" width="2" height="2" fill="#e3e3e3"/><rect x="19" y="11" width="2" height="2" fill="#e3e3e3"/><rect x="5" y="12" width="2" height="2" fill="#e3e3e3"/></svg>COMMERCIAL
    </div>
    <div class="tab" style="top:115px">
      <svg viewBox="0 0 26 26" fill="#111"><path d="M3 24V14l6-5 6 5v10h-4v-6H7v6z"/><rect x="17" y="4" width="6" height="20"/><circle cx="20" cy="4" r="3"/></svg>AGRICULTURAL
    </div>
    <div class="cat-copy">
      <h2>Lorem Ipsum has been the industry's standard dummy text ever since the been the industry's&nbsp; 1500s.</h2>
      <p>simply dummy text of the printing and typesetting industry. Lorem Ipsum has been the industry's standard dummy text ever since the 1500s, when an unknown printer took a galley of type and scrambled it to make a type specimen book. It has survived Ipsum has been the industry's standard dummy text ever since the 1500s, when an unknown printer took a galley of type and scrambled it&nbsp; not only five centuries</p>
      <p>Ipsum has been the industry's standard dummy text ever since the 1500s, when an unk-<br>nown printer took a galley of type and scrambled it</p>
    </div>
  </div>
</section>

<h2 class="abs services-title">OUR SERVICES</h2>
<div class="abs services-rule"></div>
<div class="abs services-accent"></div>

<article class="abs service" style="left:69px;top:703px">
  <div class="service-strip"></div>
  <div class="service-icon"><svg viewBox="0 0 24 24" fill="#111"><circle cx="7" cy="8" r="3"/><circle cx="17" cy="8" r="3"/><circle cx="12" cy="11" r="3"/><path d="M2 18c0-3 2-5 5-5s5 2 5 5zM12 18c0-3 2-5 5-5s5 2 5 5zM6 21c0-3 3-6 6-6s6 3 6 6z"/></svg></div>
  <h3>PROPERTY MANAGEMENT</h3>
  <p>Lorem ipsolor sitconsectetuadipiscingelit. Donec auctorsus laoreet. Quisque soda leshendrerit rhoncus.</p>
  <a class="read-cyan">READ MORE →</a>
</article>

<article class="abs service" style="left:424px;top:703px">
  <div class="service-strip"></div>
  <div class="service-icon"><svg viewBox="0 0 24 24" fill="#111"><path d="M2 8 12 3l10 5z"/><rect x="3" y="9" width="18" height="2"/><rect x="5" y="12" width="2" height="7"/><rect x="9" y="12" width="2" height="7"/><rect x="13" y="12" width="2" height="7"/><rect x="17" y="12" width="2" height="7"/><rect x="2" y="20" width="20" height="2"/></svg></div>
  <h3>PROPERTIES NRAS</h3>
  <p>Lorem ipsolor sitconsectetuadipiscingelit. Donec auctorsus laoreet. Quisque soda leshendrerit rhoncus.</p>
  <a class="read-orange">READ MORE →</a>
</article>

<article class="abs service" style="left:69px;top:847px">
  <div class="service-strip"></div>
  <div class="service-icon"><svg viewBox="0 0 24 24" fill="#111"><rect x="3" y="2" width="2" height="20"/><rect x="3" y="4" width="18" height="2"/><rect x="8" y="8" width="13" height="10"/><rect x="10" y="10" width="9" height="6" fill="#fff"/></svg></div>
  <h3>SALE FOR PROPERTIES</h3>
  <p>Lorem ipsolor sitconsectetuadipiscingelit. Donec auctorsus laoreet. Quisque soda leshendrerit rhoncus.</p>
  <a class="read-orange">READ MORE →</a>
</article>

<article class="abs service" style="left:424px;top:845px">
  <div class="service-strip"></div>
  <div class="service-icon"><svg viewBox="0 0 24 24" fill="#111"><path d="M1 11 12 2l11 9h-3v11H4V11z"/><rect x="7" y="12" width="10" height="6" fill="#fff"/></svg></div>
  <h3>RENT FOR PROPERTIES</h3>
  <p>Lorem ipsolor sitconsectetuadipiscingelit. Donec auctorsus laoreet. Quisque soda leshendrerit rhoncus.</p>
  <a class="read-orange">READ MORE →</a>
</article>

<footer class="abs site-footer">
  <h4 class="footer-title" style="left:97px">Featured Projects</h4>
  <div class="project" style="top:65px">
    <div class="project-thumb" role="img" aria-label="Photo of a modern kitchen interior"></div>
    <div class="project-info"><div class="street">3412 Harrowfield Dr</div>Elmridge, SA<br><b>249000 €</b></div>
  </div>
  <div class="project" style="top:117px">
    <div class="project-thumb" role="img" aria-label="Photo of a bright living room interior" style="background:linear-gradient(135deg,#b08a5e,#e8dcc4 55%,#8c6a44)"></div>
    <div class="project-info"><div class="street">1030 Quarry Ave</div>Westbrook, SA<br><b>486000 €</b></div>
  </div>

  <h4 class="footer-title" style="left:318px">Contact Us</h4>
  <div class="contact-row" style="top:75px">
    <svg viewBox="0 0 10 10" fill="#9fd3ee"><path d="M5 0a3.5 3.5 0 0 1 3.5 3.5C8.5 6 5 10 5 10S1.5 6 1.5 3.5A3.5 3.5 0 0 1 5 0z"/></svg>
    <span class="label">Address:</span><span>2210 Ferncrest Rd<br>Oakvale, CA 90871<br>United States</span>
  </div>
  <div class="contact-row" style="top:112px">
    <svg viewBox="0 0 10 10" fill="#ddd"><path d="M2 0h2l1 2.5-1.5 1a5 5 0 0 0 3 3L7.5 5 10 6v2c0 1-1 2-2 2A8 8 0 0 1 0 2c0-1 1-2 2-2z"/></svg>
    <span class="label">Phone:</span><span>+1 555 014 3382</span>
  </div>
  <div class="contact-row" style="top:130px">
    <svg viewBox="0 0 10 10" fill="none" stroke="#ddd"><rect x=".5" y="2" width="9" height="6"/><path d="M.5 2 5 5.5 9.5 2"/></svg>
    <span class="label">Email:</span><span>office@brenwick-example.com</span>
  </div>
  <div class="contact-row" style="top:148px">
    <svg viewBox="0 0 10 10" fill="#9fd3ee"><circle cx="5" cy="5" r="4.5"/></svg>
    <span class="label">Skype:</span><span>brenwick.office</span>
  </div>

  <h4 class="footer-title" style="left:510px">Subscribe Newsletter</h4>
  <span class="form-label" style="top:72px">Name</span>
  <div class="form-input" style="top:69px"></div>
  <span class="form-label" style="top:104px">Email</span>
  <div class="form-input" style="top:100px"></div>
  <div class="subscribe">Subscribe</div>
</footer>

<div class="abs copyright">© 2015 BRENWICK STRUCTURES, ALL RIGHTS RESERVED.</div>

</body>
</html>
```